Email signature and business card

Australian company called Brakmere. We provide construction and maintenance services to the mining industry. I would like the design to be similar to our website theme(www.brakmere.com.au) whilst staying compact. RGB colours to include: 42,96,140 and 232,163,0 and I have attached 2 logos.

The following fields will need to be included:

Full Name
Title
Location/Project
Phone
Mobile
Fax
Email
Web site

Target Market(s)

Mining Industry

Industry/Entity Type

Construction

Requirements
Must have
• Full Name, Title, Office Address, Phone, Mobile, Fax, Email, Web address
• Back of card must include: Boilermaking, Carpentry, Concrete, Construction, Cranes, Data and Comms, Electrical, Fabrication, Fitting, Labour Hire, Plumbing, Rigging, Shutdowns

```html
<!DOCTYPE html>
<html lang="en">
<head>
<meta charset="utf-8">
<title>Brakmere Business Card</title>
<link href="https://fonts.googleapis.com/css2?family=Archivo:wght@800&family=Crimson+Text:wght@400;600&display=swap" rel="stylesheet">
<style>
  :root {
    --brand-blue: #2a608c;
    --brand-gold: #e8a300;
    --card-dark: #191c1d;
    --card-white: #ffffff;
    --backdrop: #dfe3e3;
    --text-light: #e9ecec;
  }
  * { box-sizing: border-box; margin: 0; padding: 0; }
  html, body { width: 1200px; height: 1200px; overflow: hidden; }
  body {
    background: var(--backdrop);
    font-family: "Crimson Text", Georgia, serif;
  }
  .card {
    position: absolute;
    left: 130px;
    width: 940px;
    height: 520px;
    overflow: hidden;
    box-shadow: 0 6px 18px rgba(0,0,0,0.15);
  }
  .card--front { top: 60px; background: var(--card-white); }
  .card--back { top: 620px; background: var(--card-dark); }

  /* shared brand mark: plain circle above the name */
  .brand-mark {
    display: flex; flex-direction: column; align-items: center; gap: 10px;
  }
  .brand-mark__dot { border-radius: 50%; background: var(--brand-blue); }
  .brand-mark__name {
    font-family: "Archivo", Arial, sans-serif;
    font-weight: 800; color: var(--brand-blue); letter-spacing: 1px; line-height: 1;
  }

  /* front */
  .front__band {
    position: absolute; left: 0; right: 0; top: 240px; bottom: 0;
    background: var(--card-dark);
  }
  .front__rule {
    position: absolute; top: 60px; height: 180px; width: 6px;
    background: var(--brand-gold);
  }
  .front__rule--a { left: 78px; }
  .front__rule--b { left: 100px; }
  .front__identity { position: absolute; left: 148px; top: 164px; }
  .front__name {
    font-family: "Archivo", Arial, sans-serif;
    font-weight: 800; font-size: 34px; letter-spacing: 1px;
    color: var(--brand-blue); line-height: 1;
  }
  .front__title {
    margin-top: 4px; margin-left: 110px;
    font-size: 17px; font-weight: 600; color: var(--brand-gold);
  }
  .card--front .brand-mark { position: absolute; right: 70px; top: 40px; }
  .card--front .brand-mark__dot { width: 110px; height: 110px; }
  .card--front .brand-mark__name { font-size: 28px; }

  .front__web {
    position: absolute; right: 60px; top: 290px;
    display: flex; align-items: center; gap: 8px;
    font-size: 17px; color: var(--text-light);
  }
  .contact-list {
    position: absolute; left: 150px; top: 300px;
    list-style: none;
  }
  .contact-list li {
    display: flex; align-items: center; gap: 14px;
    font-size: 18px; color: var(--text-light); line-height: 32px;
  }
  .icon { width: 18px; height: 18px; flex: none; }

  /* back */
  .back__rule {
    position: absolute; left: 0; right: 0; height: 6px;
    background: var(--brand-gold);
  }
  .back__rule--t1 { top: 52px; }
  .back__rule--t2 { top: 72px; }
  .back__rule--b1 { bottom: 72px; }
  .back__rule--b2 { bottom: 52px; }
  .back__content {
    position: absolute; left: 40px; right: 40px; top: 100px; bottom: 100px;
    display: flex; flex-direction: column; align-items: center; justify-content: center;
    gap: 26px;
  }
  .card--back .brand-mark__dot { width: 130px; height: 130px; }
  .card--back .brand-mark__name { font-size: 38px; }
  .services {
    text-align: center;
    font-size: 17px; line-height: 26px; color: var(--text-light);
    letter-spacing: 0.3px;
  }
  .services__sep { color: var(--brand-gold); padding: 0 6px; }
</style>
</head>
<body>

<section class="card card--front" aria-label="Business card front">
  <div class="front__rule front__rule--a"></div>
  <div class="front__rule front__rule--b"></div>

  <div class="front__identity">
    <div class="front__name">JOHN NAME</div>
    <div class="front__title">Managing Director</div>
  </div>

  <div class="brand-mark">
    <span class="brand-mark__dot"></span>
    <span class="brand-mark__name">BRAKMERE</span>
  </div>

  <div class="front__band"></div>

  <div class="front__web">
    <svg class="icon" viewBox="0 0 20 20" fill="none" stroke="var(--brand-gold)" stroke-width="1.8"><circle cx="10" cy="10" r="8"/><path d="M2 10h16M10 2c3 3 3 13 0 16M10 2c-3 3-3 13 0 16"/></svg>
    www.brakmere.com.au
  </div>

  <ul class="contact-list">
    <li>
      <svg class="icon" viewBox="0 0 20 20" fill="var(--brand-gold)"><path d="M5 2l3 4-2 2c1 2 3 4 5 5l2-2 4 3-2 3C9 17 3 11 2 5z"/></svg>
      08-5550192
    </li>
    <li>
      <svg class="icon" viewBox="0 0 20 20" fill="var(--brand-gold)"><rect x="5" y="1" width="10" height="18" rx="2"/><rect x="7" y="4" width="6" height="10" fill="var(--card-dark)"/></svg>
      0400.555.017
    </li>
    <li>
      <svg class="icon" viewBox="0 0 20 20" fill="var(--brand-gold)"><rect x="2" y="8" width="16" height="9" rx="1"/><rect x="5" y="2" width="10" height="7"/></svg>
      08.5550.193
    </li>
    <li>
      <svg class="icon" viewBox="0 0 20 20" fill="none" stroke="var(--brand-gold)" stroke-width="2"><circle cx="10" cy="10" r="3"/><path d="M13 10v1.5a2.5 2.5 0 0 0 5 0V10a8 8 0 1 0-3 6"/></svg>
      office@brakmere.com.au
    </li>
    <li>
      <svg class="icon" viewBox="0 0 20 20" fill="var(--brand-gold)"><path d="M10 1a6 6 0 0 0-6 6c0 5 6 12 6 12s6-7 6-12a6 6 0 0 0-6-6z"/><circle cx="10" cy="7" r="2.2" fill="var(--card-dark)"/></svg>
      brakmere site project WA.
    </li>
  </ul>
</section>

<section class="card card--back" aria-label="Business card back">
  <div class="back__rule back__rule--t1"></div>
  <div class="back__rule back__rule--t2"></div>
  <div class="back__content">
    <div class="brand-mark">
      <span class="brand-mark__dot"></span>
      <span class="brand-mark__name">BRAKMERE</span>
    </div>
    <p class="services">
      Boilermaking<span class="services__sep">|</span>Carpentry<span class="services__sep">|</span>Concrete<span class="services__sep">|</span>Construction<span class="services__sep">|</span>Cranes<span class="services__sep">|</span>Data and Comms<span class="services__sep">|</span>Electrical<br>
      Fabrication<span class="services__sep">|</span>Fitting<span class="services__sep">|</span>Labour Hire<span class="services__sep">|</span>Plumbing<span class="services__sep">|</span>Rigging<span class="services__sep">|</span>Shutdowns
    </p>
  </div>
  <div class="back__rule back__rule--b1"></div>
  <div class="back__rule back__rule--b2"></div>
</section>

</body>
</html>
```